Website design for Silver Harbor Trading Inc

We are looking to build a website for our company. We are a scrap metal recycling company based out of Los Angeles. We purchase scrap metal in the US and ship them to China for recycling into fresh metal ores to supply industrial users. We would designs that emphasize the color green given our name and the nature of our business. Recycling themes are welcomed. We already have a URL at:
http://silverharbortradinginc.example/
At this point, I would like 4 pages:
- Home page
- About Us
- Resources
- Contact us
Our sister company is Maple Crest Intl Inc and they have a website that we can use as a starting point.
http://www.maplecrest-intl.example/
Our competitor has a website below. However we dislike the design given we believe it looks rather dull.
http://www.orientalloysalvage.example/en/
Lastly, this is for a website shell only. Please design the template, graphics, and color schemes. We will write the contents later.

```html
<!DOCTYPE html>
<html lang="en">
<head>
<meta charset="utf-8">
<title>Silver Harbor Trading – Resources</title>
<link rel="stylesheet" href="https://fonts.googleapis.com/css2?family=Roboto:wght@300;400;500;700&display=swap">
<style>
:root{
  --green:#6aab1c;
  --green-bright:#7dc322;
  --bar:#3a3a3a;
  --header:#1f1f1f;
  --footer:#1a1a1a;
  --panel:#ffffff;
  --box:#f5f5f5;
  --ink:#333333;
  --muted:#8a8a8a;
  --carrier:#4a4a4a;
  --rule:#dddddd;
}
*{margin:0;padding:0;box-sizing:border-box}
html,body{width:1171px;height:1200px;overflow:hidden}
body{position:relative;font-family:'Roboto',sans-serif;font-weight:300;background:#222;color:var(--ink)}
.news-bar{position:absolute;left:0;top:0;width:1171px;height:33px;background:var(--bar);color:#ddd;font-size:11.5px;display:flex;align-items:center;padding-left:238px;gap:12px;white-space:nowrap}
.news-bar .label{color:var(--green);font-size:15px;font-weight:400}
.site-header{position:absolute;left:0;top:33px;width:1171px;height:90px;background:var(--header)}
.brand{position:absolute;left:184px;top:30px;display:flex;align-items:center;gap:8px;font-size:24px;font-weight:500;color:#fff}
.brand .mark{width:26px;height:26px;border-radius:50%;background:var(--green)}
.main-nav{position:absolute;left:641px;top:36px;display:flex;gap:14px;font-size:15px;color:#fff;font-weight:400}
.main-nav .sep{color:#aaa}
.main-nav .active{color:var(--green-bright)}
.backdrop{position:absolute;left:0;top:123px;width:1171px;height:1002px;
  background:linear-gradient(180deg,#6f85a8 0%,#9c7c9c 18%,#d99a86 36%,#f0b07a 48%,#c98a72 58%,#34527f 80%,#1d3a66 92%,#9a3a2e 100%)}
.slider{position:absolute;left:189px;top:159px;width:790px;height:338px;background:#fff;box-shadow:0 1px 4px rgba(0,0,0,.3)}
.slide{position:absolute;left:7px;top:7px;width:777px;height:324px;
  background:linear-gradient(110deg,#3a3a36 0%,#5a4b45 25%,#6b6258 42%,#8fb0cf 62%,#a8cdee 80%,#8fbfe8 100%)}
.slide-caption{position:absolute;left:35px;top:275px;font-size:21px;color:#fff}
.slide-arrow{position:absolute;top:148px;width:30px;height:30px}
.slide-arrow.prev{left:13px;opacity:.5}
.slide-arrow.next{left:731px}
.content{position:absolute;left:184px;top:515px;width:803px;height:566px;background:var(--panel)}
.section-title{position:absolute;left:7px;font-size:21px;color:var(--green);font-weight:400}
.section-rule{position:absolute;left:7px;width:789px;height:1px;background:var(--rule)}
.res-box{position:absolute;background:var(--box);border-radius:3px;padding:20px 17px}
.res-box h3{font-size:15.5px;font-weight:400;color:var(--ink);margin-bottom:10px;white-space:nowrap}
.res-box li{list-style:none;font-size:11.5px;color:var(--muted);line-height:21.5px}
.carriers{position:absolute;left:0;width:803px;display:flex;align-items:center;justify-content:center;gap:34px}
.carrier{font-size:20px;font-weight:500;color:var(--carrier);white-space:nowrap}
.site-footer{position:absolute;left:0;top:1125px;width:1171px;height:75px;background:var(--footer);color:#ddd;text-align:center}
.footer-nav{margin-top:10px;font-size:11.5px;font-weight:400;display:flex;justify-content:center;gap:12px}
.footer-legal{margin-top:14px;font-size:10.5px;color:#aaa;display:flex;justify-content:center;gap:10px}
</style>
</head>
<body>
<div class="news-bar"><span class="label">Latest News :</span><span>Last update: 23/08/2013 &nbsp;| &nbsp;16:05</span><span style="margin-left:14px">Lorem Ipsum is simply dummy text of the printing and typesetting industry.</span></div>

<header class="site-header">
  <div class="brand"><span class="mark"></span><span>Silver Harbor Trading</span></div>
  <nav class="main-nav"><span>Home</span><span class="sep">|</span><span>About us</span><span class="sep">|</span><span class="active">Resources</span><span class="sep">|</span><span>Contact us</span></nav>
</header>

<div class="backdrop" role="img" aria-label="Sunset sky over a container ship loaded with cargo containers"></div>

<section class="slider">
  <div class="slide" role="img" aria-label="Pile of crushed scrap metal under a bright blue sky with sunlight"></div>
  <div class="slide-caption">Scrap Metal Resource</div>
  <svg class="slide-arrow prev" viewBox="0 0 30 30"><circle cx="15" cy="15" r="15" fill="#555"/><path d="M17 9l-6 6 6 6" stroke="#fff" stroke-width="3" fill="none"/></svg>
  <svg class="slide-arrow next" viewBox="0 0 30 30"><circle cx="15" cy="15" r="15" fill="#444"/><path d="M13 9l6 6-6 6" stroke="#fff" stroke-width="3" fill="none"/></svg>
</section>

<main class="content">
  <h2 class="section-title" style="top:20px">Resources</h2>
  <div class="section-rule" style="top:50px"></div>

  <div class="res-box" style="left:8px;top:65px;width:251px;height:133px"><h3>TERMINAL</h3><ul><li>Harbor Point Terminals</li><li>Bayview</li><li>Portline</li></ul></div>
  <div class="res-box" style="left:275px;top:65px;width:251px;height:133px"><h3 style="margin-bottom:7px">TRAIL</h3><ul><li style="line-height:19.5px">Western Rail</li><li style="line-height:19.5px">Plains Rail</li><li style="line-height:19.5px">Coastal Rail</li><li style="line-height:19.5px">Southern Rail</li></ul></div>
  <div class="res-box" style="left:543px;top:65px;width:251px;height:199px"><h3>SERVICES</h3><ul><li>Daily Currencies Exchange</li><li>Maps and Directions</li><li>Today's Weather</li><li>The Official US Time</li><li>World Map-Atlas Maps</li><li>Worldtime Finder</li></ul></div>
  <div class="res-box" style="left:8px;top:205px;width:251px;height:59px;padding:6px 21px"><h3 style="margin-bottom:6px">IMPORTER SECURITY FILING</h3><ul><li>ISF website</li></ul></div>
  <div class="res-box" style="left:275px;top:205px;width:251px;height:59px;padding:6px 20px"><h3 style="margin-bottom:2px">PORT PASS</h3><ul><li>Los Angeles</li></ul></div>

  <h2 class="section-title" style="top:290px">Carrier Website</h2>
  <div class="section-rule" style="top:319px"></div>

  <div class="carriers" style="top:348px">
    <span class="carrier">Pacifica Lines</span>
    <span class="carrier">Azur Marine</span>
    <span class="carrier">Eastwind Container Lines</span>
    <span class="carrier">Nordstar</span>
  </div>
  <div class="carriers" style="top:428px">
    <span class="carrier">Evertide Line</span>
    <span class="carrier">Hanbit</span>
    <span class="carrier">Apex Line</span>
    <span class="carrier">Kaiyo Line</span>
  </div>
  <div class="carriers" style="top:505px">
    <span class="carrier">Strait Line</span>
    <span class="carrier">Orion Line</span>
    <span class="carrier">Sunhai</span>
  </div>
</main>

<footer class="site-footer">
  <nav class="footer-nav"><span>Home</span><span>|</span><span>About us</span><span>|</span><span>Resources</span><span>|</span><span>Contact us</span></nav>
  <div class="footer-legal"><span>©2013 Company Name , All Rights Reserved</span><span>|</span><span>Privacy Policy</span><span>|</span><span>Terms &amp; Conditions</span></div>
</footer>
</body>
</html>
```